Business card for builder specialising in renovations.

Need a card for our building business. Business name is under Martin Powles.
Have licence number on card ( 527691K)
Contact number (0400 382 415)
Want to work on logo for some business cards and shirts - something with MP or MPB or open to ideas??
No animations, No hammers. Something sharp and eye catching.
Highlight that we are a renovation specialist. Simple on front with extra details on back with some lines to jot down things.

Target Market(s)

Renovators

Industry/Entity Type

Building

Contact Information for Business Card

2 sided with room on back to jot things down.
Extra details on back so front can be simple ..like, renovations, bathrooms, decks, extensions, new builds,

Logo Text

MP

Font styles to use
Serif

Requirements
Must have
• Eye catching design .
• Name : Martin powles
• Licence number
• Contact number - 0400382415
Nice to have
• Some logo design that we can carry through to other forms of advertising
• Local builder
• Quality work
Should not have
• No animations

```html
<!DOCTYPE html>
<html lang="en">
<head>
<meta charset="utf-8">
<title>Martin Powles – Business Card</title>
<link href="https://fonts.googleapis.com/css2?family=Open+Sans:wght@400;600;700&display=swap" rel="stylesheet">
<style>
  :root {
    --backdrop: #3b332f;
    --card-dark: #1f1f1f;
    --card-light: #ffffff;
    --orange: #f7941d;
    --grey: #8c8c8c;
    --white: #ffffff;
    --shadow: rgba(0, 0, 0, 0.45);
  }
  * { margin: 0; padding: 0; box-sizing: border-box; }
  html, body {
    width: 1200px;
    height: 716px;
    overflow: hidden;
    background: var(--backdrop);
    font-family: "Open Sans", Arial, sans-serif;
  }
  .canvas {
    position: relative;
    width: 1200px;
    height: 716px;
  }
  .card {
    position: absolute;
    top: 203px;
    width: 540px;
    height: 310px;
    border-radius: 4px;
    overflow: hidden;
    box-shadow: 0 10px 30px var(--shadow);
  }

  /* Back of card */
  .card-back {
    left: 30px;
    background: var(--card-light);
  }
  .brand {
    position: absolute;
    display: flex;
    align-items: center;
    gap: 12px;
  }
  .brand-dot {
    border-radius: 50%;
    background: var(--orange);
  }
  .brand-name {
    font-weight: 700;
    color: var(--grey);
    letter-spacing: 1px;
  }
  .card-back .brand { left: 36px; top: 40px; }
  .card-back .brand-dot { width: 46px; height: 46px; }
  .card-back .brand-name { font-size: 40px; }

  .notes {
    position: absolute;
    left: 200px;
    right: 36px;
    top: 48px;
    list-style: none;
  }
  .notes li {
    height: 28px;
    border-bottom: 1.5px solid var(--orange);
  }
  .services {
    position: absolute;
    right: 36px;
    bottom: 30px;
    text-align: right;
    color: var(--orange);
    font-weight: 600;
    font-size: 15px;
    line-height: 1.35;
  }

  /* Front of card */
  .card-front {
    left: 630px;
    background: var(--card-dark);
  }
  .skyline {
    position: absolute;
    left: 20px;
    top: 0;
    width: 330px;
    height: 220px;
    background: linear-gradient(160deg, #2e2e2e 0%, #262626 60%, #1f1f1f 100%);
  }
  .card-front .brand { left: 40px; top: 70px; }
  .card-front .brand-dot { width: 56px; height: 56px; }
  .card-front .brand-name { font-size: 50px; }

  .owner-name {
    position: absolute;
    left: 270px;
    top: 86px;
    font-size: 30px;
    font-weight: 700;
    letter-spacing: 1px;
    text-transform: uppercase;
  }
  .owner-first { color: var(--orange); }
  .owner-last { color: var(--grey); }

  .contact-band {
    position: absolute;
    left: 0;
    right: 0;
    bottom: 0;
    height: 96px;
    background: var(--orange);
    border-top-left-radius: 16px;
    padding: 14px 36px 0 40px;
    color: var(--white);
  }
  .phone {
    font-size: 34px;
    font-weight: 700;
    letter-spacing: 1px;
    line-height: 1.1;
  }
  .licence {
    font-size: 20px;
    font-weight: 400;
    margin-top: 4px;
  }
</style>
</head>
<body>
  <main class="canvas">
    <section class="card card-back" aria-label="Card back">
      <div class="brand">
        <span class="brand-dot"></span>
        <span class="brand-name">MPB</span>
      </div>
      <ul class="notes" aria-label="Lines for notes">
        <li></li><li></li><li></li><li></li><li></li><li></li>
      </ul>
      <p class="services">Renovation Specialist, Bathrooms<br>Decks, Extensions, New builds</p>
    </section>

    <section class="card card-front" aria-label="Card front">
      <div class="skyline" role="img" aria-label="Faint photograph of building facades"></div>
      <div class="brand">
        <span class="brand-dot"></span>
        <span class="brand-name">MPB</span>
      </div>
      <h1 class="owner-name"><span class="owner-first">Martin</span> <span class="owner-last">Powles</span></h1>
      <div class="contact-band">
        <p class="phone">0400 382 415</p>
        <p class="licence">Licence number 527691K</p>
      </div>
    </section>
  </main>
</body>
</html>
```